Electronic Letterhead for The Harborline Partners, LLC

I would like to have an electronic letterhead layout using Word for first and second page letterhead using my previously designed logo. The logo was successfully designed by a designer for the Pixel Bazaar. I would like to only use the "C" portion of the logo on the second page. I would like the designer that designed my logo to be included in the designers that participate in this competition.

Target Market(s)

My clients are typically governmental entities or financial entities

Industry/Entity Type

Electronic

Font styles to use
Sans Serif

Requirements
Must have
• Utilize existing logo
Nice to have
• Fist and second page letterhead design in electronic format (Word)

```html
<!DOCTYPE html>
<html lang="en">
<head>
<meta charset="utf-8">
<title>The Harborline Partners, LLC — Letterhead</title>
<link rel="stylesheet" href="https://fonts.googleapis.com/css2?family=Crimson+Text:wght@400;600&display=swap">
<style>
  :root {
    --backdrop: #e4e4e4;
    --paper: #ffffff;
    --brand-blue: #2d4f8f;
    --ink: #4a4a4a;
    --rule: #9a9a9a;
    --bar-grey: #d3d3d3;
  }
  * { box-sizing: border-box; margin: 0; padding: 0; }
  html, body {
    width: 1200px;
    height: 800px;
    overflow: hidden;
    background: var(--backdrop);
    font-family: "Crimson Text", Georgia, serif;
  }
  .sheet {
    position: absolute;
    top: 110px;
    width: 410px;
    height: 576px;
    background: var(--paper);
  }
  .sheet--first { left: 165px; }
  .sheet--second { left: 612px; }

  .letterhead-name {
    position: absolute;
    top: 38px;
    right: 26px;
    display: flex;
    align-items: center;
    gap: 8px;
    color: var(--brand-blue);
    font-size: 15px;
    font-weight: 400;
    line-height: 1.1;
    text-align: left;
  }
  .letterhead-name__dot {
    width: 12px;
    height: 12px;
    border-radius: 50%;
    background: var(--brand-blue);
    flex: none;
  }

  .footer {
    position: absolute;
    left: 12px;
    right: 26px;
    bottom: 10px;
    display: flex;
    align-items: center;
    justify-content: space-between;
  }
  .footer__bar {
    width: 96px;
    height: 17px;
    background: var(--bar-grey);
  }
  .footer__contacts {
    display: flex;
    align-items: stretch;
    font-size: 8px;
    line-height: 11.5px;
    color: var(--ink);
  }
  .contact-group {
    padding: 0 6px;
    border-left: 1px solid var(--rule);
  }
  .contact-group:first-child { border-left: none; padding-left: 0; }
  .contact-group:last-child { padding-right: 0; }
  .contact-group--address { text-align: right; }
  .contact-line {
    display: flex;
    align-items: center;
    gap: 4px;
    white-space: nowrap;
  }
  .contact-group--address .contact-line { justify-content: flex-end; }
  .icon {
    width: 6px;
    height: 6px;
    flex: none;
    fill: var(--brand-blue);
  }
</style>
</head>
<body>

  <section class="sheet sheet--first" aria-label="First page letterhead">
    <header class="letterhead-name">
      <span class="letterhead-name__dot"></span>
      <span>The Harborline<br>Partners, LLC</span>
    </header>
    <footer class="footer">
      <div class="footer__bar"></div>
      <div class="footer__contacts">
        <div class="contact-group contact-group--address">
          <div class="contact-line"><svg class="icon" viewBox="0 0 10 10"><path d="M5 0a3.5 3.5 0 0 0-3.5 3.5C1.5 6 5 10 5 10s3.5-4 3.5-6.5A3.5 3.5 0 0 0 5 0zm0 5a1.4 1.4 0 1 1 0-2.8A1.4 1.4 0 0 1 5 5z"/></svg>214 Pierpoint Lane</div>
          <div class="contact-line">Seabrook, Texas 77586</div>
        </div>
        <div class="contact-group">
          <div class="contact-line"><svg class="icon" viewBox="0 0 10 10"><path d="M2 0l2 2.5-1 1.2a6 6 0 0 0 3.3 3.3l1.2-1L10 8 8.5 10C4 9.5.5 6 0 1.5z"/></svg>281-555-0142</div>
          <div class="contact-line"><svg class="icon" viewBox="0 0 10 10"><path d="M2 0h6v3H2zM0 3.5h10V8H8v2H2V8H0zm3 3V9h4V6.5z"/></svg>281-555-0187</div>
        </div>
        <div class="contact-group">
          <div class="contact-line"><svg class="icon" viewBox="0 0 10 10"><path d="M0 2h10v6H0zm1 .6L5 5.6l4-3z" fill-rule="evenodd"/></svg>info@harborlinepartners.com</div>
          <div class="contact-line"><svg class="icon" viewBox="0 0 10 10"><path d="M5 0a5 5 0 1 0 0 10A5 5 0 0 0 5 0zm0 1.2c.8.8 1.2 2.2 1.3 3.3H3.7C3.8 3.4 4.2 2 5 1.2zM3.7 5.5h2.6C6.2 6.6 5.8 8 5 8.8 4.2 8 3.8 6.6 3.7 5.5z"/></svg>www.harborlinepartners.com</div>
        </div>
      </div>
    </footer>
  </section>

  <section class="sheet sheet--second" aria-label="Second page letterhead">
    <footer class="footer">
      <div class="footer__bar"></div>
      <div class="footer__contacts">
        <div class="contact-group contact-group--address">
          <div class="contact-line"><svg class="icon" viewBox="0 0 10 10"><path d="M5 0a3.5 3.5 0 0 0-3.5 3.5C1.5 6 5 10 5 10s3.5-4 3.5-6.5A3.5 3.5 0 0 0 5 0zm0 5a1.4 1.4 0 1 1 0-2.8A1.4 1.4 0 0 1 5 5z"/></svg>214 Pierpoint Lane</div>
          <div class="contact-line">Seabrook, Texas 77586</div>
        </div>
        <div class="contact-group">
          <div class="contact-line"><svg class="icon" viewBox="0 0 10 10"><path d="M2 0l2 2.5-1 1.2a6 6 0 0 0 3.3 3.3l1.2-1L10 8 8.5 10C4 9.5.5 6 0 1.5z"/></svg>281-555-0142</div>
          <div class="contact-line"><svg class="icon" viewBox="0 0 10 10"><path d="M2 0h6v3H2zM0 3.5h10V8H8v2H2V8H0zm3 3V9h4V6.5z"/></svg>281-555-0187</div>
        </div>
        <div class="contact-group">
          <div class="contact-line"><svg class="icon" viewBox="0 0 10 10"><path d="M0 2h10v6H0zm1 .6L5 5.6l4-3z" fill-rule="evenodd"/></svg>info@harborlinepartners.com</div>
          <div class="contact-line"><svg class="icon" viewBox="0 0 10 10"><path d="M5 0a5 5 0 1 0 0 10A5 5 0 0 0 5 0zm0 1.2c.8.8 1.2 2.2 1.3 3.3H3.7C3.8 3.4 4.2 2 5 1.2zM3.7 5.5h2.6C6.2 6.6 5.8 8 5 8.8 4.2 8 3.8 6.6 3.7 5.5z"/></svg>www.harborlinepartners.com</div>
        </div>
      </div>
    </footer>
  </section>

</body>
</html>
```